Dietitian needs awesome business card

I need a contemporary design that's eye catching but professional.
My card is to given to doctors, specialists and patients alike.
I manage patients with chronic diseases
I have uploaded my logo and current business card, I would also like the other Certified Clinical Nutritionist logo incorporated into the design

Target Market(s)

Doctors, specialists and patients

Industry/Entity Type

Healthcare

Contact Information for Business Card

www.brightfieldnutrition.com.au
Ph: 0427 561 903
Fax: 6457 2183
email: marcus.k.diet@fernmail.com
Space on the back of the card with: Appointment date, Appointment time and appointment location

Font styles to use
Serif

Colors
fbee3e
876aae
ffc214

Requirements
Must have
• My Logo
• Certified Clinical Nutritionist Logo
• My 4 locations - Pinebrook Medical Centre, North Corrin Health, Hollis Medical, Ashcombe Doctors Surgery
Nice to have
• I like the colours in my current business card

```html
<!DOCTYPE html>
<html lang="en">
<head>
<meta charset="utf-8">
<title>Brightfield Nutrition &amp; Dietetics – Business Card</title>
<link rel="stylesheet" href="https://fonts.googleapis.com/css2?family=Open+Sans:wght@400;600;700&display=swap">
<style>
  :root {
    --bg: #3a3431;
    --card-white: #ffffff;
    --green: #6cbf1e;
    --green-light: #9ad83a;
    --green-dark: #4f9e12;
    --navy: #1f2f8a;
    --text: #222222;
    --orange: #f07a22;
  }
  * { box-sizing: border-box; margin: 0; padding: 0; }
  html, body { width: 1200px; height: 844px; overflow: hidden; }
  body {
    background: var(--bg);
    font-family: "Open Sans", Arial, sans-serif;
    display: flex; align-items: center; justify-content: center; gap: 48px;
  }
  .card {
    width: 520px; height: 300px; position: relative; overflow: hidden;
    box-shadow: 0 10px 28px rgba(0,0,0,.45);
  }
  /* Front */
  .card-front { background: var(--card-white); padding: 52px 40px 30px 44px; }
  .brand { display: flex; align-items: center; gap: 12px; }
  .brand-dot { width: 46px; height: 46px; border-radius: 50%; background: var(--green); flex: none; }
  .brand-name { font-weight: 600; font-size: 24px; color: var(--navy); line-height: 1.1; }
  .holder { margin-top: 28px; font-size: 18px; font-weight: 700; color: var(--green); }
  .contacts { list-style: none; margin-top: 10px; }
  .contacts li { display: flex; align-items: center; gap: 10px; font-size: 14px; color: var(--text); line-height: 21px; }
  .contacts svg { width: 11px; height: 11px; fill: var(--green); flex: none; }
  .credentials { margin-top: 10px; font-size: 14px; font-weight: 700; color: var(--green); }
  .badge { position: absolute; right: 44px; top: 110px; width: 54px; height: 58px; background: var(--orange); }
  /* Back */
  .card-back {
    background: linear-gradient(135deg, var(--green-light), var(--green) 55%, var(--green-dark));
  }
  .appointment {
    position: absolute; left: 0; top: 0; width: 100%; height: 150px;
    background: var(--card-white); padding: 34px 44px 0;
    border-top: 10px solid var(--green-light);
  }
  .field-row { display: flex; gap: 18px; margin-bottom: 18px; }
  .field { flex: 1; display: flex; align-items: flex-end; gap: 6px; font-size: 13px; color: var(--green); }
  .field .line { flex: 1; border-bottom: 1px dotted var(--green); height: 1px; margin-bottom: 3px; }
  .notice { font-size: 12px; font-weight: 700; color: var(--green-dark); }
  .back-swoosh {
    position: absolute; left: 60px; top: 120px; width: 400px; height: 170px; border-radius: 50%;
    background: radial-gradient(ellipse at center, rgba(255,255,255,.22), rgba(255,255,255,0) 70%);
  }
  .back-brand {
    position: absolute; left: 0; right: 0; top: 190px; text-align: center;
    font-weight: 600; font-size: 30px; color: var(--card-white);
  }
</style>
</head>
<body>
  <section class="card card-front">
    <div class="brand">
      <span class="brand-dot"></span>
      <span class="brand-name">Brightfield Nutrition &amp; Dietetics</span>
    </div>
    <div class="badge" role="img" aria-label="Professional accreditation badge"></div>
    <p class="holder">Marcus Kellaway</p>
    <ul class="contacts">
      <li><svg viewBox="0 0 12 12"><path d="M2 1l2 0 1 3-1.5 1a6 6 0 0 0 2.5 2.5L7 6l3 1v2c0 1-1 2-2 2A8 8 0 0 1 1 3c0-1 1-2 1-2z"/></svg>0427 561 903</li>
      <li><svg viewBox="0 0 12 12"><rect x="2" y="1" width="8" height="10" rx="1"/></svg>6457 2183</li>
      <li><svg viewBox="0 0 12 12"><path d="M1 3h10v7H1z"/></svg>marcus.k.diet@fernmail.com</li>
      <li><svg viewBox="0 0 12 12"><circle cx="6" cy="6" r="5"/></svg>www.brightfieldnutrition.com.au</li>
    </ul>
    <p class="credentials">Certified Clinical Nutritionist, Nutritionist and Chef</p>
  </section>

  <section class="card card-back">
    <div class="appointment">
      <div class="field-row">
        <span class="field">Date: <span class="line"></span></span>
        <span class="field">Time: <span class="line"></span></span>
      </div>
      <div class="field-row">
        <span class="field">Location: <span class="line"></span></span>
      </div>
      <p class="notice">If unable to keep appointment, kindly give 24hrs notice.</p>
    </div>
    <div class="back-swoosh" role="img" aria-label="Soft decorative leaf swoosh"></div>
    <p class="back-brand">Brightfield Nutrition &amp; Dietetics</p>
  </section>
</body>
</html>
```